Ridgeline Journeys business card

please see website
www.ridgelinejourneys.comau

info needed on card
Curtis Halvey
Ph
email
Adventure Riding GPS trails

please use my logo and colours off my site

Curtis Halvey
curtis@ridgelinejourneys.com

```html
<!DOCTYPE html>
<html lang="en">
<head>
<meta charset="utf-8">
<title>Ridgeline Journeys – Business Card</title>
<link rel="stylesheet" href="https://fonts.googleapis.com/css2?family=Open+Sans:wght@400;600;700;800&display=swap">
<style>
  :root {
    --backdrop: #3a3431;
    --card-black: #161616;
    --card-black-light: #2a2a2a;
    --panel-black: #0e0e0e;
    --brand-yellow: #ffe21a;
    --brand-yellow-deep: #f2c400;
    --text-white: #f2f2f2;
    --tab-grey: #c8c8c8;
  }
  * { box-sizing: border-box; margin: 0; padding: 0; }
  html, body {
    width: 1200px; height: 844px; overflow: hidden;
    background: var(--backdrop);
    font-family: "Open Sans", Arial, sans-serif;
  }
  .stage {
    position: relative; width: 1200px; height: 844px;
    display: flex; align-items: center; justify-content: center; gap: 50px;
  }
  .card {
    position: relative; width: 520px; height: 298px; overflow: hidden;
    background: radial-gradient(ellipse at 40% 40%, var(--card-black-light), var(--card-black) 70%);
    box-shadow: 0 12px 30px rgba(0,0,0,.45);
  }

  /* Front */
  .band {
    position: absolute; left: 0; right: 0;
    background: linear-gradient(90deg, var(--brand-yellow-deep), var(--brand-yellow));
  }
  .band--top { top: 0; height: 12px; }
  .band--bottom { bottom: 0; height: 14px; }

  .diagonal-panel {
    position: absolute; inset: 0; width: 100%; height: 100%;
  }

  .identity {
    position: absolute; right: 190px; top: 84px; text-align: right;
  }
  .identity__name {
    color: var(--brand-yellow); font-weight: 700; font-size: 19px; letter-spacing: .3px;
    text-transform: uppercase; padding-bottom: 2px;
    border-bottom: 1.5px solid var(--brand-yellow);
  }
  .identity__role { color: var(--text-white); font-size: 14px; margin-top: 2px; }

  .contact {
    position: absolute; right: 190px; top: 176px; text-align: right;
    color: var(--text-white); font-size: 13.5px; line-height: 1.35;
  }

  /* Back */
  .tab {
    position: absolute; width: 26px; height: 48px;
    background: linear-gradient(90deg, var(--brand-yellow-deep), var(--brand-yellow));
  }
  .tab::after {
    content: ""; position: absolute; top: 0; bottom: 0; width: 5px; background: var(--tab-grey);
  }
  .tab--left { left: 0; top: 145px; }
  .tab--left::after { right: 0; }
  .tab--right { right: 0; top: 14px; }
  .tab--right::after { left: 0; }

  .brand {
    position: absolute; left: 130px; top: 96px;
    display: flex; align-items: center; gap: 18px;
  }
  .brand__mark { width: 40px; height: 40px; background: var(--brand-yellow); }
  .brand__name {
    color: var(--text-white); font-weight: 800; font-size: 30px; line-height: 1;
    text-transform: uppercase; letter-spacing: .5px;
  }
  .brand__url {
    position: absolute; left: 188px; top: 188px;
    color: var(--brand-yellow); font-size: 12.5px; font-weight: 600;
  }
  .brand__tagline {
    position: absolute; left: 188px; top: 210px;
    color: var(--text-white); font-size: 12px; letter-spacing: .3px;
  }
</style>
</head>
<body>
<main class="stage">
  <section class="card card--front" aria-label="Card front">
    <svg class="diagonal-panel" viewBox="0 0 520 298" aria-hidden="true">
      <polygon points="410,12 520,12 520,284 330,284" fill="var(--panel-black)"/>
      <polygon points="400,12 412,12 332,284 320,284" fill="var(--brand-yellow)"/>
    </svg>
    <div class="band band--top"></div>
    <div class="identity">
      <p class="identity__name">Curtis Halvey</p>
      <p class="identity__role">Managing Director</p>
    </div>
    <div class="contact">
      <p>044-318-2265</p>
      <p>curtis@ridgelinejourneys.com</p>
      <p>www.ridgelinejourneys.comau</p>
    </div>
    <div class="band band--bottom"></div>
  </section>

  <section class="card card--back" aria-label="Card back">
    <div class="tab tab--right"></div>
    <div class="tab tab--left"></div>
    <div class="brand">
      <span class="brand__mark"></span>
      <p class="brand__name">Ridgeline<br>Journeys</p>
    </div>
    <p class="brand__url">www.ridgelinejourneys.comau</p>
    <p class="brand__tagline">Adventure Riding GPS trails</p>
  </section>
</main>
</body>
</html>
```